Web landing page design

- Create a Web Design (Uncoded - PSD layout only)

We need a single web page design to promote our service. This page will
acts as a landing page for users and also be utilized in social media
advertising. Please provide us with a cutting edge design. I have attached
a link for what the company is about. In essence we are a photo checking
service which reviews photos for retailers, hotels abd car dealerships to
check everything is good after a service has been performed. Whether it be
a new promotion, cleaning or just checking prices. I am looking for a
design to say that we do many photos and at a very cost effective price
(team based in Mexico)

Link: https://slidevault.example/view/qTr8nWx2LpZk4mHcYdJs/
*Deadline*
5 days
*Updates*

- The Start Here box needs to look like this:

-Start Here (heading)
-A box for email addresses to be entered
-Then a check box with "Yes, I have read and agree to the Privacy Policy
and agree to receive email marketing from Plumora88'
-A submit button

All of this information needs to be in one box please. And please feel
free to contact me if you have any questions about this.

*Target Market(s)*
Retail business, Merchandising companies, Rental property owners, Car
dealers
Updates

Please can you submit entries. I am just looking for a tidy to a presentation already created. Just needs design touches.

Target Market(s)

Ability for audience to understand concept quickly
Benefits to why to use the product stand out
Technology driven approach

Industry/Entity Type

Retail

Number of Pages Required

1 page

Colors
0792cd

Requirements
Must have
• Clean and modern design

```html
<!DOCTYPE html>
<html lang="en">
<head>
<meta charset="utf-8">
<title>clarivo – Start Here</title>
<link href="https://fonts.googleapis.com/css2?family=Open+Sans:wght@400;600;700&display=swap" rel="stylesheet">
<style>
  :root {
    --brand: #0792cd;
    --brand-deep: #1580c4;
    --ink: #111111;
    --white: #ffffff;
    --field-text: #555555;
  }
  * { box-sizing: border-box; margin: 0; padding: 0; }
  html, body { width: 1200px; height: 867px; overflow: hidden; background: var(--white); }
  body { font-family: "Open Sans", Arial, sans-serif; position: relative; }

  .hero { position: absolute; left: 0; top: 0; width: 1200px; height: 592px; overflow: hidden; }
  .hero-photo {
    position: absolute; inset: 0;
    background:
      linear-gradient(rgba(40,38,42,0.45), rgba(40,38,42,0.45)),
      radial-gradient(ellipse 260px 340px at 830px 300px, #6b4f43 0%, rgba(107,79,67,0) 100%),
      linear-gradient(90deg, #7a7a7e 0%, #9a9799 35%, #7f6e68 60%, #8c8486 100%);
  }

  .brand-name { position: absolute; left: 75px; top: 50px; font-size: 28px; font-weight: 600; color: var(--white); line-height: 34px; }

  .main-nav { position: absolute; top: 56px; left: 756px; }
  .main-nav a { position: absolute; white-space: nowrap; color: var(--white); text-decoration: none; font-weight: 700; font-size: 16px; line-height: 22px; }

  .signup { position: absolute; left: 317px; top: 196px; width: 567px; }
  .signup h1 { text-align: center; color: var(--white); font-size: 48px; font-weight: 700; line-height: 64px; letter-spacing: 0.5px; }
  .signup-field { display: flex; margin-top: 22px; height: 43px; }
  .signup-field .email { flex: 1; border: 0; border-radius: 22px 0 0 22px; background: var(--white); padding-left: 20px; font: 600 14px "Open Sans", sans-serif; color: var(--field-text); display: flex; align-items: center; }
  .signup-field .submit { width: 118px; border: 0; border-radius: 0 22px 22px 0; background: var(--brand-deep); color: var(--white); font: 700 15px "Open Sans", sans-serif; letter-spacing: 0.5px; }
  .consent { display: flex; margin-top: 31px; margin-left: 13px; color: var(--white); font-size: 15px; font-weight: 400; line-height: 24px; }
  .consent .box { flex: none; width: 15px; height: 15px; margin: 6px 18px 0 0; background: linear-gradient(#ffffff, #c9c9c9); border: 1px solid #999; }
  .consent p { width: 495px; }

  .slider-arrows { position: absolute; left: 558px; top: 484px; }

  .stats { position: absolute; top: 0; left: 0; width: 1200px; }
  .stat { position: absolute; top: 651px; width: 240px; text-align: center; }
  .stat-value { display: block; color: var(--brand-deep); font-weight: 700; font-size: 54px; line-height: 64px; }
  .stat-label { display: block; color: var(--ink); font-weight: 700; font-size: 14.5px; line-height: 24px; }

  .site-footer { position: absolute; left: 0; top: 816px; width: 1200px; height: 51px; background: var(--brand-deep); color: var(--white); font-size: 13.5px; font-weight: 700; }
  .site-footer .legal { position: absolute; left: 0; right: 0; top: 15px; line-height: 20px; text-align: center; }
  .site-footer .legal span { margin: 0 10px; }
  .site-footer .code { position: absolute; left: 1151px; top: 14px; line-height: 20px; }
</style>
</head>
<body>
  <header class="hero">
    <div class="hero-photo" role="img" aria-label="Blurred photo of a smiling shopper holding shopping bags in a bright mall"></div>

    <span class="brand-name">clarivo</span>

    <nav class="main-nav">
      <a style="left:0">ABOUT</a>
      <a style="left:93px">RESULTS</a>
      <a style="left:201px">HOW</a>
      <a style="left:280px">FREE TRIAL</a>
    </nav>

    <section class="signup">
      <h1>START HERE</h1>
      <div class="signup-field">
        <div class="email">Your Email Address</div>
        <button class="submit">SUBMIT</button>
      </div>
      <div class="consent">
        <span class="box"></span>
        <p>Yes, I have read and agree to the Privacy Policy and agree to receive email marketing from Plumora88'</p>
      </div>
    </section>

    <svg class="slider-arrows" width="84" height="44" viewBox="0 0 84 44" aria-label="Slide controls">
      <polyline points="22,2 2,22 22,42" fill="none" stroke="#fff" stroke-width="2"/>
      <polyline points="62,2 82,22 62,42" fill="none" stroke="#fff" stroke-width="2"/>
    </svg>
  </header>

  <section class="stats">
    <div class="stat" style="left:78px;top:642px"><span class="stat-value">2.2m</span><span class="stat-label">Photos reviewed<br>last year</span></div>
    <div class="stat" style="left:346px"><span class="stat-value">5p</span><span class="stat-label">From per photo<br>reviewed</span></div>
    <div class="stat" style="left:615px"><span class="stat-value">97.2%</span><span class="stat-label">Average Compliance</span></div>
    <div class="stat" style="left:883px"><span class="stat-value">3-8%</span><span class="stat-label">Sales increase.</span></div>
  </section>

  <footer class="site-footer">
    <p class="legal">Copyright © 2018. Company Name .All Right Reserved<span>|</span>Privacy Policy<span>|</span>Terms</p>
    <span class="code">M1</span>
  </footer>
</body>
</html>
```